Business Card for a Dental Office

The design should communicate integrity, quality and reliability. We also want the card look elegant, simple, but still stand out, different from the traditional-dental-office business card.

Industry/Entity Type

Business

```html
<!DOCTYPE html>
<html lang="en">
<head>
<meta charset="utf-8">
<title>Harwick Dental Studio – Business Card</title>
<link rel="stylesheet" href="https://fonts.googleapis.com/css2?family=Open+Sans:wght@400;600;700&display=swap">
<style>
  :root {
    --backdrop: #e8e5df;
    --card-white: #ffffff;
    --card-black: #0b0b0b;
    --ink-dark: #2b2b2b;
    --ink-grey: #6a6a6a;
    --gold: #b08a1e;
    --yellow: #e4d21c;
    --soft-white: #e6e6e6;
  }
  * { margin: 0; padding: 0; box-sizing: border-box; }
  html, body {
    width: 1200px; height: 843px; overflow: hidden;
    background: var(--backdrop);
    font-family: "Open Sans", Arial, sans-serif;
  }
  .stage {
    position: relative; width: 1200px; height: 843px;
    display: flex; align-items: center; justify-content: center; gap: 48px;
  }
  .card {
    position: relative; width: 540px; height: 309px;
    border-radius: 6px; overflow: hidden;
    box-shadow: 0 10px 24px rgba(0,0,0,.25);
  }

  /* Back side */
  .card-back {
    background: linear-gradient(135deg, #1c1c1c 0%, var(--card-black) 55%, #050505 100%);
    display: flex; flex-direction: column; align-items: center; justify-content: center;
  }
  .back-brand {
    display: flex; align-items: center; gap: 12px;
    color: var(--soft-white); font-weight: 600; font-size: 26px;
    letter-spacing: 1px; text-transform: uppercase;
  }
  .brand-square { width: 26px; height: 26px; background: var(--yellow); }
  .back-web {
    position: absolute; bottom: 26px; left: 0; right: 0; text-align: center;
    color: #9a9a9a; font-size: 13px; letter-spacing: 1px;
  }

  /* Front side */
  .card-front { background: var(--card-white); }
  .front-brand {
    position: absolute; top: 50px; left: 150px;
  }
  .front-brand-name {
    display: flex; align-items: center; gap: 10px;
    color: var(--ink-dark); font-weight: 700; font-size: 22px;
    letter-spacing: .5px; text-transform: uppercase; line-height: 1;
  }
  .front-brand-name .brand-square { width: 22px; height: 22px; background: var(--ink-dark); }
  .tagline {
    margin-top: 5px; padding-left: 32px;
    color: var(--gold); font-weight: 700; font-size: 10.5px;
    letter-spacing: .6px; text-transform: uppercase;
  }
  .person {
    position: absolute; top: 118px; right: 290px; text-align: right;
  }
  .person-name { color: var(--ink-dark); font-weight: 700; font-size: 18px; line-height: 1.2; }
  .person-title { color: var(--gold); font-size: 13px; line-height: 1.35; }
  .person-address { color: var(--ink-grey); font-size: 13px; line-height: 1.35; }
  .contacts {
    position: absolute; top: 124px; left: 268px; list-style: none;
  }
  .contacts li {
    display: flex; align-items: center; gap: 9px;
    color: var(--ink-grey); font-size: 13px; line-height: 19px;
  }
  .contacts svg { width: 12px; height: 12px; fill: var(--ink-dark); flex: none; }
  .front-band { position: absolute; left: 0; bottom: 0; width: 540px; height: 309px; }
</style>
</head>
<body>
<main class="stage">

  <section class="card card-back" aria-label="Card back">
    <div class="back-brand"><span class="brand-square"></span>Harwick Dental Studio</div>
    <p class="back-web">www.harwickdental.com</p>
  </section>

  <section class="card card-front" aria-label="Card front">
    <svg class="front-band" viewBox="0 0 540 309" preserveAspectRatio="none" aria-hidden="true">
      <path d="M0 210 Q260 275 540 232 L540 309 L0 309 Z" fill="var(--card-black)"/>
      <path d="M0 216 Q260 281 540 238" fill="none" stroke="var(--yellow)" stroke-width="2.5"/>
    </svg>

    <div class="front-brand">
      <div class="front-brand-name"><span class="brand-square"></span>Harwick Dental Studio</div>
      <p class="tagline">Your smile is your gift to others</p>
    </div>

    <div class="person">
      <p class="person-name">Daniel Reyes</p>
      <p class="person-title">CEO/Founder</p>
      <p class="person-address">4120 Juniper Court</p>
      <p class="person-address">Fairbanks, Alaska 99701</p>
    </div>

    <ul class="contacts">
      <li><svg viewBox="0 0 12 12"><path d="M2.5 0.5l2 2.5-1 1.3c.7 1.6 1.9 2.8 3.5 3.5l1.3-1 2.5 2-1.2 2.2C5 10.5 1.5 7 .4 1.7z"/></svg>907 555 0142</li>
      <li><svg viewBox="0 0 12 12"><path d="M3 0h6a1 1 0 0 1 1 1v10a1 1 0 0 1-1 1H3a1 1 0 0 1-1-1V1a1 1 0 0 1 1-1zm.6 1.5v8h4.8v-8z"/></svg>907 555 0187</li>
      <li><svg viewBox="0 0 12 12"><path d="M0 2h12v8H0zm1.2 1.2v.3L6 6.6l4.8-3.1v-.3z"/></svg>hello@harwickdental.com</li>
      <li><svg viewBox="0 0 12 12"><circle cx="6" cy="6" r="5.5"/><path d="M.5 6h11M6 .5c-2.2 2.5-2.2 8.5 0 11M6 .5c2.2 2.5 2.2 8.5 0 11" stroke="#fff" stroke-width=".8" fill="none"/></svg>www.harwickdental.com</li>
    </ul>
  </section>

</main>
</body>
</html>
```